Fast-casual chicken restaurant Crisp Harbor needs a catering menu design

We need a catering menu designed for Crisp Harbor. We are looking to design a 24x36in landscape menu board for our new catering menu. The catering memo attached includes our catering menu and Crisp Harbor branding. More information about our brand can be found at https://crispharbor-eats.example/.

```html
<!DOCTYPE html>
<html lang="en">
<head>
<meta charset="utf-8">
<title>Catering Menu Board</title>
<link href="https://fonts.googleapis.com/css2?family=Montserrat:wght@700;800;900&display=swap" rel="stylesheet">
<style>
:root{
  --page:#f4f4f4;
  --board:#232323;
  --panel:#141414;
  --yellow:#f6c52c;
  --yellow-soft:#f3d66a;
  --red:#d8382a;
  --grey-head:#5b6067;
  --line:#777;
  --white:#ffffff;
  --bbq:#6b6f74;
  --teri:#485a72;
  --ink:#111;
}
*{box-sizing:border-box;margin:0;padding:0}
html,body{width:957px;height:1200px;overflow:hidden;background:var(--page)}
body{font-family:"Montserrat",sans-serif;font-weight:800;color:var(--white)}
.board{position:absolute;left:20px;top:294px;width:917px;height:611px;background:var(--board)}
.deal{position:absolute;top:14px;width:430px;height:168px}
.deal.packaged{left:18px}
.deal.per-person{left:469px}
.deal-banner{display:grid;grid-template-columns:116px 198px 116px;height:69px}
.photo{display:block}
.photo.fried{background:linear-gradient(135deg,#e9e6e0,#d6652c 45%,#b8421d 70%,#f0ece6)}
.photo.platter{background:linear-gradient(135deg,#7a3a1e,#c9592a 40%,#d9a24a 70%,#5b3a24)}
.deal-title{background:var(--yellow);color:var(--red);font-weight:900;font-size:28px;line-height:29px;text-align:center;display:flex;align-items:center;justify-content:center}
.deal-table{border:2px solid var(--yellow);border-top:none;background:var(--panel)}
.row{display:grid;grid-template-columns:65px 68px 231px 62px;align-items:center}
.per-person .row{grid-template-columns:66px 66px 232px 62px}
.row>span{border-right:1px solid var(--line);height:100%;display:flex;align-items:center;padding:0 7px}
.row>span:last-child{border-right:none;justify-content:center}
.row .c{justify-content:center}
.thead{background:var(--grey-head);height:24px;font-size:13.5px}
.thead>span{justify-content:flex-start}
.thead>span:nth-child(2){justify-content:center}
.trow{height:25px;font-size:13.5px}
.trow .name{font-size:8.5px;line-height:9px;flex-direction:column;align-items:flex-start;justify-content:center}
.per-person .trow .name{align-items:center}
.trow .name small{font-size:5px;font-weight:700}
.trow .items{font-size:9px;line-height:10px;font-weight:700}
.trow .price{font-size:14px}
.a-la-carte{position:absolute;left:18px;top:198px;width:881px;height:206px}
.a-la-carte .photo{position:absolute;inset:0;background:linear-gradient(90deg,#c8481f 0%,#d5d7d6 26%,#cfd1d0 70%,#c24420 88%,#b8401c 100%)}
.carte-menu{position:absolute;left:229px;top:0;width:422px;height:206px}
.carte-title{height:31px;background:var(--red);text-align:center;font-size:27px;font-weight:900;line-height:31px}
.carte-grid{display:grid;grid-template-columns:180px 129px 113px}
.carte-head{background:#000;height:19px;font-size:13px;color:var(--yellow);line-height:19px;padding-left:12px}
.carte-head:nth-child(2){padding-left:13px}
.carte-col{background:linear-gradient(90deg,var(--yellow),var(--yellow-soft));height:156px;padding:5px 0 0 12px;color:var(--ink);font-size:14px;line-height:18.6px;border-right:1px solid var(--ink)}
.carte-col:nth-child(5){padding-left:26px}
.carte-col.prices{background:linear-gradient(90deg,var(--yellow-soft),rgba(243,214,106,.2));border-right:none;padding-left:25px}
.flavors{position:absolute;left:18px;top:418px;display:grid;grid-template-columns:repeat(5,169px);column-gap:9px}
.flavor-col{border:1.5px solid var(--white);border-bottom:none;height:193px;background:var(--panel);text-align:center}
.flavor-head{background:var(--white);height:31px;font-size:22.5px;font-weight:900;line-height:31px}
.flavor-list{list-style:none;padding-top:10px;font-size:13.5px;line-height:13.5px}
.flavor-list li{margin-bottom:13.5px;padding:0 4px}
.h-flavors{color:var(--yellow)}
.h-bbq{color:var(--bbq)}
.h-rubs{color:var(--red)}
.h-teri{color:var(--teri)}
.h-buffalo{color:var(--ink)}
</style>
</head>
<body>
<main class="board">
  <section class="deal packaged">
    <div class="deal-banner">
      <span class="photo fried" role="img" aria-label="Fried tenders, wings and waffle fries on a platter"></span>
      <h2 class="deal-title">PACKAGED<br>DEALS</h2>
      <span class="photo fried" role="img" aria-label="Plate of sauced chicken wings"></span>
    </div>
    <div class="deal-table">
      <div class="row thead"><span>NAME</span><span>FEEDS</span><span>ITEMS</span><span>PRICE</span></div>
      <div class="row trow"><span class="name">FAMILY</span><span class="c">4</span><span class="items">12 tenders, Sauces, Dressing, Large side, 2L</span><span class="price">$24.99</span></div>
      <div class="row trow"><span class="name">TAILGATE</span><span class="c">10</span><span class="items">20 Tenders, 30 Wings, Sauces, Dressings, 1 Party side</span><span class="price">$75.99</span></div>
      <div class="row trow"><span class="name">HOUSE PARTY</span><span class="c">10</span><span class="items">20 Tenders, 60 Wings, Sauces, 2 Party sides, 2 Party Salads, Dressings, 2 2L</span><span class="price">$155.99</span></div>
    </div>
  </section>

  <section class="deal per-person">
    <div class="deal-banner">
      <span class="photo platter" role="img" aria-label="Spread of wings, onion rings and sides on a table"></span>
      <h2 class="deal-title">PER PERSON<br>DEALS</h2>
      <span class="photo platter" role="img" aria-label="Bowl of dry-rub chicken wings"></span>
    </div>
    <div class="deal-table">
      <div class="row thead"><span>NAME</span><span>FEEDS</span><span>ITEMS</span><span>PRICE</span></div>
      <div class="row trow"><span class="name">SNACK<small>(PER PERSON)</small></span><span class="c">1</span><span class="items">2 tenders, Sauce, Dressing, 1 reg side</span><span class="price">$7.99</span></div>
      <div class="row trow"><span class="name">PARTY<small>(PER PERSON)</small></span><span class="c">1</span><span class="items">2 Tenders, 3 Wings, Sauce, Dressing, 1 reg side, 12oz/fountain drink</span><span class="price">$11.99</span></div>
      <div class="row trow"><span class="name">FEAST<small>(PER PERSON)</small></span><span class="c">1</span><span class="items">2 Tenders, 6 Wings, Sauce, Dressing, 1 reg side, Dessert, 20 oz drink</span><span class="price">$15.99</span></div>
    </div>
  </section>

  <section class="a-la-carte">
    <span class="photo" role="img" aria-label="Plates of sauced chicken tenders on a concrete surface with dipping cups"></span>
    <div class="carte-menu">
      <h2 class="carte-title">A LA CARTE</h2>
      <div class="carte-grid">
        <div class="carte-head">ITEMS</div>
        <div class="carte-head">INCREMENTS</div>
        <div class="carte-head">PRICE</div>
        <div class="carte-col">Wings<br>Tenders<br>Waffle Fries<br>Garlic Pram Tots<br>Chicken Caesar Salad<br>Caesar Salad<br>Any Sauce<br>Cheese Sauce</div>
        <div class="carte-col">50, 75, 100<br>30, 45, 60<br>Party Size<br>Party Size<br>Party Size<br>Party Size<br>8 oz<br>8 oz</div>
        <div class="carte-col prices">$xx.xx<br>$xx.xx<br>$13.99<br>$13.99<br>$38.99<br>$27.99<br>$1.99<br>$2.49</div>
      </div>
    </div>
  </section>

  <section class="flavors">
    <div class="flavor-col"><h3 class="flavor-head h-flavors">FLAVORS</h3>
      <ul class="flavor-list"><li>HONEY MUSTARD</li><li>HOT LEMON PEPPER</li><li>JAMAICAN JERK</li><li>MANGO HABANERO</li><li>SWEET CHILI</li></ul></div>
    <div class="flavor-col"><h3 class="flavor-head h-bbq">BBQ</h3>
      <ul class="flavor-list"><li>CAJUN BBQ</li><li>CITRUS CHIPOTLE</li><li>GOLDEN BBQ</li><li>HONEY BBQ</li><li>KICKIN BBQ</li></ul></div>
    <div class="flavor-col"><h3 class="flavor-head h-rubs">DRY RUBS</h3>
      <ul class="flavor-list"><li>7 PEPPER</li><li>CAJUN</li><li>GARLIC PARM</li><li>LEMON PEPPER</li><li>WEST TEXAS<br>MESQUITE</li></ul></div>
    <div class="flavor-col"><h3 class="flavor-head h-teri">TERIYAKI</h3>
      <ul class="flavor-list"><li>CAJUN TERIYAKI</li><li>SPICY TERIYAKI</li><li>TRADITIONAL<br>TERIYAKI</li></ul></div>
    <div class="flavor-col"><h3 class="flavor-head h-buffalo">BUFFALO</h3>
      <ul class="flavor-list"><li>MILD BREEZE</li><li>COASTAL CLIMB</li><li>RED FLARE</li><li>ROCKET HEAT</li><li>INFERNO BLAST</li></ul></div>
  </section>
</main>
</body>
</html>
```